Local fast-growing company in the service sector

We are looking for a modern business card design, which should also appear on our letterheads

Target Market(s)

Private and industrial sectors

Contact Information for Business Card

Vorname Name
Kellberger Str. 18
74523 Feldhausen
Tel.: 07146-839214-0
Name@agentur-kvtl.de

Colors
9d9d9d
919191
aaaaaa

Requirements
Must have
• The logo (file) in silver

```html
<!DOCTYPE html>
<html lang="de">
<head>
<meta charset="utf-8">
<title>KVTL – Visitenkarte</title>
<link rel="stylesheet" href="https://fonts.googleapis.com/css2?family=Open+Sans:wght@400;600;700&display=swap">
<style>
  :root {
    --bg: #e9e8e6;
    --card-white: #fbfbfb;
    --silver-light: #d6d6d6;
    --silver-mid: #aaaaaa;
    --silver: #9d9d9d;
    --silver-dark: #919191;
    --text-dark: #4a4a4a;
    --text: #5c5c5c;
  }
  * { margin: 0; padding: 0; box-sizing: border-box; }
  html, body {
    width: 1200px; height: 844px; overflow: hidden;
    background: var(--bg);
    font-family: "Open Sans", Arial, sans-serif;
  }
  .stage {
    width: 1200px; height: 844px;
    display: flex; align-items: center; justify-content: center; gap: 60px;
  }
  .card {
    position: relative;
    width: 510px; height: 330px;
    border-radius: 4px;
    box-shadow: 0 6px 18px rgba(0,0,0,.18);
    overflow: hidden;
  }
  .card--front { background: var(--card-white); }
  .card--back {
    background: linear-gradient(135deg, #f2f2f2 0%, var(--silver-light) 35%, var(--silver-mid) 70%, #8a8a8a 100%);
    display: flex; align-items: center; justify-content: center;
  }
  .brand {
    position: absolute; top: 78px; left: 180px;
    display: flex; align-items: center; gap: 16px;
  }
  .brand__square {
    width: 54px; height: 54px;
    background: var(--silver);
  }
  .brand__name {
    font-weight: 700; font-size: 58px; line-height: 1;
    color: var(--silver); letter-spacing: 1px;
  }
  .card--back .brand__name {
    font-size: 72px; color: #f4f4f4;
  }
  .contact {
    position: absolute; left: 42px; bottom: 38px;
    color: var(--text);
  }
  .contact__name {
    font-weight: 700; font-size: 19px; color: var(--text-dark);
    letter-spacing: .5px; margin-bottom: 8px;
  }
  .contact__line {
    display: flex; align-items: center; gap: 9px;
    font-size: 15px; line-height: 22px;
  }
  .contact__icon { width: 13px; height: 13px; fill: var(--text-dark); flex: none; }
  .contact__address { font-size: 15px; margin-top: 10px; }
</style>
</head>
<body>
<main class="stage">
  <section class="card card--front" aria-label="Vorderseite">
    <div class="brand">
      <span class="brand__square"></span>
      <span class="brand__name">KVTL</span>
    </div>
    <div class="contact">
      <p class="contact__name">VORNAME NAME</p>
      <p class="contact__line">
        <svg class="contact__icon" viewBox="0 0 16 16" aria-hidden="true"><path d="M3.6 1.2l2.3 2.6-1.3 2a9 9 0 0 0 5.6 5.6l2-1.3 2.6 2.3-1.5 2.4C7.6 14.6 1.4 8.4 1.2 2.7z"/></svg>
        07146-839214-0
      </p>
      <p class="contact__line">
        <svg class="contact__icon" viewBox="0 0 16 16" aria-hidden="true"><path d="M1 3h14v10H1z M2 4l6 5 6-5" fill="none" stroke="#4a4a4a" stroke-width="1.6"/></svg>
        Name@agentur-kvtl.de
      </p>
      <p class="contact__line">
        <svg class="contact__icon" viewBox="0 0 16 16" aria-hidden="true"><circle cx="8" cy="8" r="7"/><path d="M1 8h14M8 1c-3 3-3 11 0 14M8 1c3 3 3 11 0 14" fill="none" stroke="#fbfbfb" stroke-width="1"/></svg>
        www.agentur-kvtl.de
      </p>
      <p class="contact__address">Kellberger Str. 18 74523 Feldhausen</p>
    </div>
  </section>
  <section class="card card--back" aria-label="Rückseite">
    <span class="brand__name">KVTL</span>
  </section>
</main>
</body>
</html>
```